BuildLinkHub.com Full Stationery Design

Business Card will have all info on it. Letterhead will not have name, title or mobile number. Keep general feeling very clean, using colors from the logo as accents.
Name:Dale Marchetti
Title:President
Phone: 1-800-555-0142
Cell: 306-555-0187
email: dale@buildlinkhub.example
website: www.buildlinkhub.example
Address:
PO Box 947
Cedarvale, NR
S0J2T0

Target Market(s)

Construction Business owners

Industry/Entity Type

Business

Contact Information for Business Card

Name:Dale Marchetti
Title:President
Phone: 1-800-555-0142
Cell: 306-555-0187
Address:
PO Box 947
Cedarvale, NR
S0J2T0

Font styles to use
Sans Serif

Requirements
Must have
• Clean look
Should not have
• Images or cartoon type characters or tools

```html
<!DOCTYPE html>
<html lang="en">
<head>
<meta charset="utf-8">
<title>BuildLinkHub.com Business Card</title>
<link href="https://fonts.googleapis.com/css2?family=Open+Sans:wght@400;600;700&display=swap" rel="stylesheet">
<style>
  :root {
    --backdrop: #e9e7e3;
    --paper: #ffffff;
    --slate: #4b596b;
    --accent-red: #e8262d;
    --accent-orange: #f47b20;
    --text-on-dark: #ffffff;
    --text-muted: #4a4f57;
    --pattern-grey: #eef0f2;
    --pattern-pink: #fbe9e6;
  }
  * { box-sizing: border-box; margin: 0; padding: 0; }
  html, body { width: 1200px; height: 987px; overflow: hidden; }
  body {
    background: var(--backdrop);
    font-family: "Open Sans", Arial, sans-serif;
    position: relative;
  }
  .card {
    position: absolute;
    left: 293px;
    width: 615px;
    height: 350px;
    background: var(--paper);
    overflow: hidden;
    box-shadow: 0 2px 6px rgba(0,0,0,0.18);
  }
  .card--front { top: 131px; }
  .card--back { top: 505px; }

  .front-band { position: absolute; inset: 0; width: 100%; height: 100%; }

  .wordmark {
    position: absolute;
    display: flex;
    align-items: center;
    gap: 12px;
    color: var(--slate);
    font-weight: 700;
    white-space: nowrap;
  }
  .wordmark__square { display: block; background: var(--accent-orange); }
  .card--front .wordmark {
    top: 62px; left: 0; right: 0;
    justify-content: center;
    font-size: 34px;
  }
  .card--front .wordmark__square { width: 30px; height: 30px; }

  .holder {
    position: absolute;
    left: 33px;
    top: 225px;
    color: var(--text-on-dark);
  }
  .holder__name { font-size: 22px; font-weight: 600; line-height: 28px; }
  .holder__title { font-size: 17px; line-height: 22px; margin-bottom: 6px; }
  .holder__address { font-style: normal; font-size: 16px; line-height: 24px; padding-left: 2px; }

  .contact-list {
    position: absolute;
    right: 31px;
    top: 226px;
    list-style: none;
    color: var(--text-on-dark);
    font-size: 15.5px;
  }
  .contact-list li {
    display: flex;
    justify-content: flex-end;
    align-items: center;
    gap: 7px;
    height: 23.5px;
  }
  .contact-list svg { width: 15px; height: 15px; flex: none; }

  .back-pattern {
    position: absolute;
    inset: 0;
    background: linear-gradient(135deg, var(--pattern-grey) 0%, var(--pattern-pink) 50%, var(--pattern-grey) 100%);
  }
  .card--back .wordmark {
    top: 128px; left: 0; right: 0;
    justify-content: center;
    font-size: 40px;
  }
  .card--back .wordmark__square { width: 36px; height: 36px; }
  .back-url {
    position: absolute;
    top: 290px; left: 0; right: 0;
    text-align: center;
    font-size: 16px;
    color: var(--text-muted);
  }
</style>
</head>
<body>

<section class="card card--front" aria-label="Business card front">
  <svg class="front-band" viewBox="0 0 615 350" preserveAspectRatio="none" aria-hidden="true">
    <defs>
      <radialGradient id="slateGlow" cx="0.5" cy="0.75" r="0.7">
        <stop offset="0" stop-color="#66768a"/>
        <stop offset="1" stop-color="#4a586a"/>
      </radialGradient>
    </defs>
    <polygon points="0,110 307,254 615,110 615,350 0,350" fill="url(#slateGlow)"/>
    <polyline points="0,106 307,250 615,106" fill="none" stroke="#f47b20" stroke-width="3"/>
    <polyline points="0,101 307,245 615,101" fill="none" stroke="#e8262d" stroke-width="2"/>
  </svg>

  <div class="wordmark">
    <span class="wordmark__square"></span>
    <span class="wordmark__name">BuildLinkHub.com</span>
  </div>

  <div class="holder">
    <p class="holder__name">Dale Marchetti</p>
    <p class="holder__title">President</p>
    <address class="holder__address">PO Box 947<br>Cedarvale, NR, S0J2T0</address>
  </div>

  <ul class="contact-list">
    <li>1-800-555-0142
      <svg viewBox="0 0 16 16" aria-hidden="true"><path fill="#fff" d="M3.6 1.5l2.3 2.6-1.3 1.8c.9 2 2.4 3.6 4.5 4.6l1.8-1.3 2.6 2.3-1.4 2.2C7.5 13.5 2.5 8.6 1.5 3z"/></svg>
    </li>
    <li>306-555-0187
      <svg viewBox="0 0 16 16" aria-hidden="true"><rect x="4" y="1" width="8" height="14" rx="1.5" fill="none" stroke="#fff" stroke-width="1.5"/><circle cx="8" cy="12.6" r="0.9" fill="#fff"/></svg>
    </li>
    <li>dale@buildlinkhub.example
      <svg viewBox="0 0 16 16" aria-hidden="true"><rect x="1" y="3.5" width="14" height="9" fill="#fff"/><polyline points="1,3.5 8,9 15,3.5" fill="none" stroke="#4b596b" stroke-width="1.2"/></svg>
    </li>
    <li>www.buildlinkhub.example
      <svg viewBox="0 0 16 16" aria-hidden="true"><circle cx="8" cy="8" r="7" fill="#fff"/><path d="M5 4.5c1.5.5 2 1.5 1.2 2.6-.8 1 .4 2.2 1.6 2 .9 2 .2 3-.6 3.8M10 3c-.4 1.4.6 2.4 2.5 2.2" fill="none" stroke="#4b596b" stroke-width="1.3"/></svg>
    </li>
  </ul>
</section>

<section class="card card--back" aria-label="Business card back">
  <div class="back-pattern" role="img" aria-label="Faint geometric pattern in light grey and soft coral tones"></div>
  <div class="wordmark">
    <span class="wordmark__square"></span>
    <span class="wordmark__name">BuildLinkHub.com</span>
  </div>
  <p class="back-url">www.buildlinkhub.example</p>
</section>

</body>
</html>
```